Nanny Share Ecommerce Website for Finding Childcare and Parents who need Childcare BrightPramHub.net

Our company needs an ecommerce website (BrightPramHub.net) for a US subscription based service strictly for nanny sharing that connects families and caregivers. The website would allow families to connect with one another as well as to search for nannies. The service would be searchable for other families by location (by radius or zip code), children demographic (age range/gender/special needs), days of week or times, after school care, school closure days (holidays), etc. The service would also be searchable for nannies based on gender, provider age range, years experience, language, hourly rate, transportation available, certification (CPR first aid), education etc. The search fields would be searchable and sortable and allow to connect with the provider (after paying subscription fee). The service would be similar to tendlyfolk.net in that it would allow for families and caregivers to post photos as well as a short bio of the themselves. There would also be a feedback/star rating mechanism to rate caregivers who have performed work for families (viewable to public). The service would be free for nannies to post their bios and only a subscription based service for families to connect with other families or with caregivers (able to view bio but need service to connect). There will be a short bio on the benefits of nanny sharing (reduced cost, increased flexibility for parents, reduced illness, increased socialization with other children vs. sole nanny), as well as Q&A section with best practices.

Target Market(s)

Families, Nannies

Industry/Entity Type

Childcare

Logo Text

Bright Pram Hub

Coding

Coded - Design and coding required

Number of Pages Required

5+ page

Requirements
Must have
• Searchable (need to be able to search for families as well as nannies), responsive, functional, easy to use, add value to families and nannies. Needs to be able to collect payment for subscription.
Nice to have
• Optimized for mobile, SEO optimized

```html
<!DOCTYPE html>
<html lang="en">
<head>
<meta charset="utf-8">
<title>Bright Pram Hub — Nanny Sharing</title>
<link rel="stylesheet" href="https://fonts.googleapis.com/css2?family=Lato:wght@400;700&family=Varela+Round&display=swap">
<style>
:root{
  --blue:#1a8fd0;
  --blue-dark:#1572b8;
  --green:#8ab53f;
  --green-dark:#6f9a2a;
  --text:#222;
  --muted:#777;
  --grey-band:#ececec;
  --footer:#0a8ed0;
  --footer-bar:#1a9ee0;
  --star:#f5a623;
  --card-btn:#dcecf6;
  --white:#fff;
}
*{box-sizing:border-box;margin:0;padding:0}
html,body{width:1200px;height:2727px;overflow:hidden}
body{position:relative;font-family:"Lato",sans-serif;color:var(--text);background:var(--white)}
.abs{position:absolute}

/* header */
.site-header{left:0;top:0;width:1200px;height:84px;background:var(--white);z-index:3}
.brand{left:118px;top:20px;font-family:"Varela Round",sans-serif;font-size:31px;color:var(--blue)}
.main-nav{right:114px;top:31px;display:flex;gap:34px;font-size:17px;font-weight:700;color:#333}
.main-nav .active{color:var(--blue)}

/* hero */
.hero{left:0;top:84px;width:1200px;height:600px;background:linear-gradient(90deg,#eef1f1 0%,#e6e9e8 45%,#dcdcd8 100%)}
.hero-photo{left:520px;top:0;width:680px;height:600px;background:radial-gradient(ellipse at 55% 45%,#e9cdb8 0%,#d8d4ce 40%,#e4e5e3 75%)}
.hero-title{left:109px;top:133px;font-family:"Varela Round",sans-serif;font-size:46px;line-height:48px;color:var(--blue)}
.hero-title .accent{color:var(--green)}
.btn{display:flex;align-items:center;justify-content:center;color:var(--white);font-weight:700;font-size:18px;height:47px;width:193px}
.btn-find-care{left:109px;top:309px;background:linear-gradient(#8fc043,#6e9e28)}
.btn-find-nannies{left:309px;top:309px;background:linear-gradient(#29a2e0,#1479b8)}
.hero-curve{left:0;top:594px;width:1200px;height:90px;z-index:2}

/* section titles */
.section-title{left:0;width:1200px;text-align:center;font-size:30px;font-weight:400;z-index:4}
.title-offer{top:680px;font-weight:700;color:#111}

/* offer cards */
.offer-card{top:738px;width:229px;height:304px;background:var(--white);border:1px solid #ddd;box-shadow:0 1px 4px rgba(0,0,0,.12)}
.offer-card .photo{position:absolute;left:6px;top:5px;width:217px;height:163px}
.offer-card h3{position:absolute;top:184px;width:100%;text-align:center;font-size:16px;font-weight:400;color:#222}
.offer-card p{position:absolute;top:212px;left:22px;right:22px;text-align:center;font-size:11px;line-height:18px;color:var(--muted)}
.offer-card .more{position:absolute;left:8px;right:8px;top:260px;height:36px;background:var(--card-btn);color:var(--blue);font-size:12px;font-weight:700;display:flex;align-items:center;justify-content:center}

/* benefits */
.benefits{left:0;top:1104px;width:1200px;height:372px;background:linear-gradient(100deg,#8cbf3f 0%,#5fa26a 40%,#1a7cbc 75%,#1572b8 100%)}
.benefits-notch{left:570px;top:1104px;width:60px;height:22px}
.title-benefits{top:1155px;color:var(--white)}
.benefit{top:1222px;width:240px;text-align:center;color:var(--white)}
.benefit .ring{width:115px;height:115px;margin:0 auto;border-radius:50%;border:3px solid var(--white);display:flex;align-items:center;justify-content:center}
.benefit .ring span{width:101px;height:101px;border-radius:50%;display:flex;align-items:center;justify-content:center}
.benefit p{margin-top:18px;font-size:19px;font-weight:700;line-height:21px}

/* feedback */
.feedback{left:0;top:1476px;width:1200px;height:420px;background:var(--grey-band)}
.title-feedback{top:1518px;color:#111}
.review{top:1578px;width:312px;height:186px;background:var(--white);box-shadow:0 1px 3px rgba(0,0,0,.08);text-align:center}
.review .quote{margin-top:18px;height:34px}
.review p{margin:10px 26px 0;font-size:12px;line-height:22px;font-style:italic;color:#555}
.review .stars{margin-top:8px;color:var(--star);font-size:22px;letter-spacing:2px}
.review::after{content:"";position:absolute;left:50%;bottom:-10px;margin-left:-10px;border:10px solid transparent;border-bottom:0;border-top-color:var(--white)}
.author{top:1790px;display:flex;align-items:center;gap:10px}
.author .avatar{width:42px;height:42px;border-radius:50%}
.author b{display:block;font-weight:400;font-size:16px;color:#444}
.author small{display:block;font-size:11px;color:#777}
.arrow{top:1654px}

/* faq */
.title-faq{top:1948px;color:#111}
.faq{left:222px;width:753px;border:2px solid #c5dca0;display:flex;align-items:center;justify-content:space-between;padding:0 18px;font-size:16px;color:var(--green-dark);background:var(--white)}
.faq-open-head{top:2009px;height:49px;background:var(--green);border-color:var(--green);color:var(--white)}
.faq-open-body{left:222px;top:2058px;width:753px;height:78px;border:2px solid #c5dca0;border-top:0;padding:14px 26px;font-size:13px;line-height:22px;color:#555}

/* footer */
.site-footer{left:0;top:2363px;width:1200px;height:302px;background:var(--footer)}
.footer-col{top:2416px;color:var(--white)}
.footer-col h4{font-size:18px;font-weight:700;margin-bottom:20px;color:var(--white)}
.footer-col li{list-style:none;font-size:13px;line-height:31px;color:var(--white)}
.contact-line{display:flex;gap:14px;font-size:13px;line-height:26px}
.social{display:flex;gap:8px}
.social span{width:40px;height:40px;border:2px solid var(--white);border-radius:50%}
.footer-bar{left:0;top:2665px;width:1200px;height:62px;background:var(--footer-bar);color:var(--white);font-size:11px;text-align:center;line-height:62px}
</style>
</head>
<body>

<header class="abs site-header">
  <div class="abs brand">Bright Pram Hub</div>
  <nav class="abs main-nav">
    <span class="active">Home</span><span>About Us</span><span>Services</span><span>Benefits</span><span>Testimonial</span><span>FAQ</span><span>Contact</span>
  </nav>
</header>

<section class="abs hero">
  <div class="abs hero-photo" role="img" aria-label="Photo of a smiling caregiver hugging an elderly woman in a bright room"></div>
  <h1 class="abs hero-title">Nanny Sharing that<br>Connects Families<br><span class="accent">and Caregivers</span></h1>
  <div class="abs btn btn-find-care">Find Care</div>
  <div class="abs btn btn-find-nannies">Find Nannies</div>
</section>
<svg class="abs hero-curve" viewBox="0 0 1200 90" preserveAspectRatio="none" aria-hidden="true">
  <path d="M0 72 Q600 -10 1200 72 L1200 90 L0 90 Z" fill="#fff"/>
  <path d="M130 56 Q600 0 1070 56" fill="none" stroke="#1a8fd0" stroke-width="4"/>
</svg>

<h2 class="abs section-title title-offer">WHAT WE OFFER</h2>

<article class="abs offer-card" style="left:129px">
  <div class="photo" role="img" aria-label="Photo of a child's hands held in an adult's hands" style="background:linear-gradient(135deg,#e7c4ae,#c99d86)"></div>
  <h3>CHILD CARE</h3>
  <p>Donec dictum lectus non odio Cras a ante vitae enim iaculis aliquam</p>
  <div class="more">READ MORE</div>
</article>
<article class="abs offer-card" style="left:369px">
  <div class="photo" role="img" aria-label="Photo of a senior woman holding a caregiver's hand" style="background:linear-gradient(135deg,#d9d6d0,#9d8f84)"></div>
  <h3>SENIOR &amp; ADULT CARE</h3>
  <p>Donec dictum lectus non odio Cras a ante vitae enim iaculis aliquam</p>
  <div class="more">READ MORE</div>
</article>
<article class="abs offer-card" style="left:605px">
  <div class="photo" role="img" aria-label="Photo of a man with his dog outdoors in sunlight" style="background:linear-gradient(135deg,#f2c75a,#c8893a)"></div>
  <h3>PET CARE</h3>
  <p>Donec dictum lectus non odio Cras a ante vitae enim iaculis aliquam</p>
  <div class="more">READ MORE</div>
</article>
<article class="abs offer-card" style="left:853px">
  <div class="photo" role="img" aria-label="Photo of a nurse caring for an elderly woman at home" style="background:linear-gradient(135deg,#e8e2da,#8fb4cf)"></div>
  <h3>HOME CARE</h3>
  <p>Donec dictum lectus non odio Cras a ante vitae enim iaculis aliquam</p>
  <div class="more">READ MORE</div>
</article>

<section class="abs benefits"></section>
<svg class="abs benefits-notch" viewBox="0 0 60 22" aria-hidden="true"><path d="M0 0 H60 L30 22 Z" fill="#fff"/><path d="M22 4 L30 11 L38 4" fill="none" stroke="#ccc" stroke-width="2"/></svg>
<h2 class="abs section-title title-benefits">BENEFITS</h2>

<div class="abs benefit" style="left:122px">
  <div class="ring"><span style="background:#4d8a1e">
    <svg width="50" height="60" viewBox="0 0 50 60" aria-hidden="true"><circle cx="25" cy="30" r="22" fill="none" stroke="#fff" stroke-width="3"/><path d="M32 20 Q25 15 19 19 Q15 24 22 28 L28 31 Q35 35 31 41 Q25 46 17 40 M25 12 V48" fill="none" stroke="#fff" stroke-width="3"/></svg>
  </span></div>
  <p>Reduced Cost</p>
</div>
<div class="abs benefit" style="left:360px">
  <div class="ring"><span style="background:#2e7a3a">
    <svg width="56" height="50" viewBox="0 0 56 50" aria-hidden="true"><circle cx="17" cy="12" r="8" fill="#fff"/><circle cx="39" cy="12" r="8" fill="#fff"/><path d="M3 42 Q3 23 17 23 Q28 23 28 34 Q28 23 39 23 Q53 23 53 42 Z" fill="#fff"/><circle cx="28" cy="30" r="5" fill="#2e7a3a"/></svg>
  </span></div>
  <p>Increased flexibility<br>for parents</p>
</div>
<div class="abs benefit" style="left:605px">
  <div class="ring"><span style="background:#1f6655">
    <svg width="50" height="44" viewBox="0 0 50 44" aria-hidden="true"><path d="M25 40 L6 21 Q-1 12 7 5 Q16 -1 25 10 Q34 -1 43 5 Q51 12 44 21 Z" fill="none" stroke="#fff" stroke-width="3.5" stroke-linejoin="round"/></svg>
  </span></div>
  <p>Reduced Illness</p>
</div>
<div class="abs benefit" style="left:813px">
  <div class="ring"><span style="background:#135d9c">
    <svg width="50" height="50" viewBox="0 0 50 50" aria-hidden="true"><g fill="none" stroke="#fff" stroke-width="3"><circle cx="37" cy="11" r="6"/><circle cx="12" cy="25" r="6"/><circle cx="37" cy="39" r="6"/><path d="M17 22 L32 14 M17 28 L32 36"/></g></svg>
  </span></div>
  <p>Increased Socialization<br>with other children<br>vs. sole nanny</p>
</div>

<section class="abs feedback"></section>
<h2 class="abs section-title title-feedback">CLIENT FEEDBACK</h2>

<svg class="abs arrow" style="left:90px" width="24" height="40" viewBox="0 0 24 40" aria-hidden="true"><path d="M20 4 L4 20 L20 36" fill="none" stroke="#aaa" stroke-width="3"/></svg>
<svg class="abs arrow" style="left:1102px" width="24" height="40" viewBox="0 0 24 40" aria-hidden="true"><path d="M4 4 L20 20 L4 36" fill="none" stroke="#aaa" stroke-width="3"/></svg>

<div class="abs review" style="left:128px">
  <svg class="quote" width="36" height="34" viewBox="0 0 36 34" aria-hidden="true"><path d="M2 32 V18 Q2 6 14 2 L15 7 Q8 10 8 16 H15 V32 Z M20 32 V18 Q20 6 32 2 L33 7 Q26 10 26 16 H33 V32 Z" fill="#1a8fd0"/></svg>
  <p>In ullamcorper est eget tempor cursus neque mi consectetuer mi a ultricies massa est sed nisl Class aptent taciti sociosqu ad</p>
  <div class="stars">★★★★</div>
</div>
<div class="abs review" style="left:453px">
  <svg class="quote" width="36" height="34" viewBox="0 0 36 34" aria-hidden="true"><path d="M2 32 V18 Q2 6 14 2 L15 7 Q8 10 8 16 H15 V32 Z M20 32 V18 Q20 6 32 2 L33 7 Q26 10 26 16 H33 V32 Z" fill="#1a8fd0"/></svg>
  <p>In ullamcorper est eget tempor cursus neque mi consectetuer mi a ultricies massa est sed nisl Class aptent taciti sociosqu ad</p>
  <div class="stars">★★★★★</div>
</div>
<div class="abs review" style="left:784px">
  <svg class="quote" width="36" height="34" viewBox="0 0 36 34" aria-hidden="true"><path d="M2 32 V18 Q2 6 14 2 L15 7 Q8 10 8 16 H15 V32 Z M20 32 V18 Q20 6 32 2 L33 7 Q26 10 26 16 H33 V32 Z" fill="#1a8fd0"/></svg>
  <p>In ullamcorper est eget tempor cursus neque mi consectetuer mi a ultricies massa est sed nisl Class aptent taciti sociosqu ad</p>
  <div class="stars">★★★★★</div>
</div>

<div class="abs author" style="left:205px"><div class="avatar" role="img" aria-label="Reviewer portrait" style="background:linear-gradient(135deg,#7fd0c8,#d9a487)"></div><div><b>By Author Name</b><small>City, Location</small></div></div>
<div class="abs author" style="left:528px"><div class="avatar" role="img" aria-label="Reviewer portrait" style="background:linear-gradient(135deg,#9aa3b2,#4b4f5c)"></div><div><b>By Author Name</b><small>City, Location</small></div></div>
<div class="abs author" style="left:862px"><div class="avatar" role="img" aria-label="Reviewer portrait" style="background:linear-gradient(135deg,#c2b29e,#6d5f52)"></div><div><b>By Author Name</b><small>City, Location</small></div></div>

<h2 class="abs section-title title-faq">FAQ</h2>
<div class="abs faq faq-open-head"><span>Q: Class aptent taciti sociosqu ad litora torquent per</span>
  <svg width="18" height="10" viewBox="0 0 18 10" aria-hidden="true"><path d="M1 9 L9 1 L17 9" fill="none" stroke="#fff" stroke-width="2"/></svg></div>
<div class="abs faq-open-body">eget tempor cursus neque mi consectetuer mi a ultricies massa est sed nisl Class aptent taciti sociosqu ad litora torquent per conubia nostra per inceptos hymenaeos Proin nulla arcu nonummy luctus</div>
<div class="abs faq" style="top:2147px;height:46px"><span>Q: Fusce tellus Sed metus augue convallis et vehicula ut pulvinar</span>
  <svg width="18" height="10" viewBox="0 0 18 10" aria-hidden="true"><path d="M1 1 L9 9 L17 1" fill="none" stroke="#aaa" stroke-width="2"/></svg></div>
<div class="abs faq" style="top:2202px;height:47px"><span>Q: Aliquam erat volutpat Quisque dignissim</span>
  <svg width="18" height="10" viewBox="0 0 18 10" aria-hidden="true"><path d="M1 1 L9 9 L17 1" fill="none" stroke="#aaa" stroke-width="2"/></svg></div>
<div class="abs faq" style="top:2256px;height:47px"><span>Q: Mauris vel lacus vitae felis vestibulum</span>
  <svg width="18" height="10" viewBox="0 0 18 10" aria-hidden="true"><path d="M1 1 L9 9 L17 1" fill="none" stroke="#aaa" stroke-width="2"/></svg></div>

<footer class="abs site-footer"></footer>
<div class="abs footer-col" style="left:189px"><h4>COMPANY</h4><ul><li>About Us</li><li>Our Services</li><li>Why Us</li><li>Our Features</li></ul></div>
<div class="abs footer-col" style="left:387px"><h4>RESOURCES</h4><ul><li>Our Blogs</li><li>Testimonials</li><li>FAQ</li><li>Contact Us</li></ul></div>
<div class="abs footer-col" style="left:620px"><h4>CONTACT INFO</h4>
  <div class="contact-line"><svg width="16" height="22" viewBox="0 0 16 22" aria-hidden="true"><path d="M8 21 Q1 12 1 8 A7 7 0 0 1 15 8 Q15 12 8 21 Z" fill="#fff"/><circle cx="8" cy="8" r="3" fill="#0a8ed0"/></svg><span>48 Maple Grove Lane<br>Austin 78704 TX</span></div>
  <div class="contact-line" style="margin-top:6px"><svg width="16" height="18" viewBox="0 0 16 18" aria-hidden="true"><path d="M3 1 L6 5 L4 8 Q6 12 9 14 L12 12 L15 15 L13 17 Q6 16 1 4 Z" fill="none" stroke="#fff" stroke-width="1.5"/></svg><span>512.555.0147</span></div>
  <div class="contact-line" style="margin-top:6px"><svg width="16" height="18" viewBox="0 0 16 18" aria-hidden="true"><rect x="1" y="4" width="14" height="10" fill="none" stroke="#fff" stroke-width="1.5"/><path d="M1 4 L8 10 L15 4" fill="none" stroke="#fff" stroke-width="1.5"/></svg><span>hello@brightpramhub.net</span></div>
</div>
<div class="abs footer-col" style="left:885px"><h4>GET IN TOUCH</h4>
  <div class="social"><span aria-label="Social link"></span><span aria-label="Social link"></span><span aria-label="Social link"></span><span aria-label="Social link"></span></div>
</div>
<div class="abs footer-bar">© 2018 Bright Pram Hub &nbsp;All right reserved &nbsp;Terms of Use</div>

</body>
</html>
```